Website Design for a different kind of Business Consulting organisation needed!

We need a website design that reflects who we are, the simplicity of our consulting business and with a focus on our priority - to help our clients deliver, or execute - the "e" in Vantor-i.

Our key high level requirements are:
1) Simple and intuitive look and feel
2) Integration with all key social media platforms, twitter, facebook, linkedin, tumblr.

10 pages, tops.
- Main page - Welcome
- About Us/ Who are Vantor-i?
- 5 services pages - Project Management, Business Process Management, Change Management, Business Analysis and Finance Systems
- Contact Us

Something like:
http://www.lumvexhold.example/

Vantor-i is a registered trademark and all Logos and other branded material are attached for reference.

So, what’s our gig: A few snippets from previous work...

We are a different kind of business consulting group. We partner with our clients to help them deliver change. We don't just provide them with the theory. We also provide them with the leadership and capability to execute the change.

We aren’t a one stop shop, and we don’t offer cookie cutter solutions. We’re a boutique consulting firm covering Project Management, Business Process Management, Change Management and Business Analytics.

Vantor-i is a professional services organisation that partners with their clients to lead the execution of strategic process and system improvement initiatives. Vantor-i combines hands on delivery with coaching in best practice methodologies and approaches to build their clients capabilities to ensure their ongoing success in project implementations.

UPDATES:

Thanks to everyone who has submitted designs so far. The standard of designs coming through is quite high, with lots of professional designs that nail the design brief. Eliminating them is proving to be quite challenging.

A few updates to the job brief:
- Please make sure the design fits on one page. We would like all of our information to be on the first page that people see without them having to scroll down
- Please ensure you include the FIVE services we offer in the design
- Please use corporate images/istock photos in your designs which are relevant to our business
- Please add a section for a live twitter feed from our twitter account and a link to google+
- Please add a section for news/updates

Also, if you are able to build a site once a design is selected, please let us know.

Thanks,

Maribel.

Target Market(s)

Our target customers are large enterprises in Australia that are growing rapidly and have recently (last 24 months) undertaken or are currently undergoing software implementations and business process improvement programs. These businesses have a turnover of $100m or above and are working hard to differentiate themselves from their competitors but are not seeing the return on investment promised by software vendors and process improvement initiatives.

Industry/Entity Type

Leadership

Requirements
Must have
• Collaboration / Training / Workshop / Consulting images all of a professional nature.
Simple, non-cluttered look with plenty of white space.

```html
<!DOCTYPE html>
<html lang="en">
<head>
<meta charset="utf-8">
<title>Vantor-i — Business Consulting</title>
<link rel="stylesheet" href="https://fonts.googleapis.com/css2?family=Open+Sans:ital,wght@0,400;0,600;0,700;1,400&display=swap">
<style>
:root{
  --brand:#0553a3;
  --ink:#3b3b3b;
  --muted:#8a8a8a;
  --nav:#8d8d8d;
  --icon-grey:#777;
  --ring:#7a7a7a;
  --white:#fff;
}
*{box-sizing:border-box;margin:0;padding:0}
html,body{width:1190px;height:1200px;overflow:hidden;background:var(--white)}
body{font-family:"Open Sans",Arial,sans-serif;color:var(--ink);position:relative}
a{color:inherit;text-decoration:none}
.top-bar{position:absolute;left:0;top:0;width:1190px;height:6px;background:var(--brand)}

.brand{position:absolute;left:118px;top:26px;display:flex;flex-direction:column;align-items:flex-end}
.brand-name{font-size:50px;font-weight:600;color:var(--brand);letter-spacing:1px;line-height:1}
.brand-sub{font-size:9px;color:var(--brand);margin-top:-2px;margin-right:74px}

.social-top{position:absolute;right:112px;top:17px;display:flex;gap:9px}
.social-top .dot{width:32px;height:32px;border-radius:50%;background:var(--icon-grey)}
.social-top .dot.active{background:var(--brand)}

.main-nav{position:absolute;left:524px;top:71px;width:545px;display:flex;justify-content:space-between;font-size:14.5px;text-transform:uppercase;line-height:22px}
.main-nav a{color:var(--nav)}
.main-nav a.current{background:var(--brand);color:var(--white);padding:0 10px}

.hero{position:absolute;left:118px;top:113px;width:951px;height:377px;
  background:linear-gradient(90deg,#1e2836 0%,#3a4553 25%,#8b949c 40%,#5d6670 55%,#1a1c1f 72%,#070707 100%)}
.hero-title{position:absolute;left:637px;top:160px;font-size:28px;font-weight:600;color:var(--white)}
.hero-dots{position:absolute;left:444px;top:357px;display:flex;gap:8px}
.hero-dots span{width:12px;height:12px;border-radius:50%;background:#c9c9c9}
.hero-dots span.on{background:var(--brand)}

.service{position:absolute;top:544px;width:200px;margin-left:-100px;text-align:center;color:#5a5a5a}
.service:nth-child(1){left:205px}
.service:nth-child(2){left:400px}
.service:nth-child(3){left:595px}
.service:nth-child(4){left:790px}
.service:nth-child(5){left:986px}
.service .badge{width:100px;height:100px;border-radius:50%;border:2px solid var(--ring);margin:0 auto 8px;display:flex;align-items:center;justify-content:center}
.service .badge i{width:50px;height:50px;border-radius:8px;background:#8a8a8a;display:block}
.service h3{font-size:20.5px;font-weight:600;line-height:28px}
.service.active{color:var(--brand)}
.service.active .badge{background:var(--brand);border-color:var(--brand)}
.service.active .badge i{background:var(--white)}

.welcome{position:absolute;left:119px;top:764px;width:570px}
.section-title{font-size:25px;font-weight:700;color:var(--brand);line-height:1.3}
.welcome p{font-size:15.5px;line-height:28px;margin-top:14px}
.tweet{margin-top:20px}
.tweet .section-title{display:flex;align-items:center;gap:10px}
.tweet .section-title::before{content:"";width:32px;height:32px;border-radius:50%;background:var(--brand)}
.tweet p{margin-top:4px}
.tweet em{color:var(--muted)}
.tweet a{color:var(--brand)}

.news{position:absolute;left:740px;top:764px;width:340px}
.news-item{margin-top:14px}
.news-item+.news-item{margin-top:26px}
.news-date{font-size:13.5px;color:var(--muted)}
.news-item h4{font-size:15.5px;font-weight:600;margin:4px 0 5px;color:#2e2e2e}
.news-item p{font-size:14px;line-height:24px}
.news-item a{color:var(--brand)}

.site-footer{position:absolute;left:0;top:1082px;width:1190px;height:118px;background:var(--brand);color:var(--white)}
.foot-col{position:absolute;top:20px;font-size:12px;line-height:19px}
.foot-col h5{font-size:13.5px;font-weight:700;letter-spacing:.3px;line-height:18px}
.foot-connect{left:119px}
.foot-social{display:flex;gap:9px;margin-top:8px}
.foot-social span{width:32px;height:32px;border-radius:50%;background:var(--white)}
.foot-pages{left:328px}
.pages-grid{display:grid;grid-template-columns:74px auto}
.foot-contact{left:563px}
.foot-brand{position:absolute;left:898px;top:18px;width:216px;text-align:right}
.foot-brand .brand-name{color:var(--white);font-size:38px;font-weight:400;display:block}
.foot-brand .brand-sub{color:var(--white);display:block;margin:-2px 66px 0 0;font-size:8px}
.foot-brand small{display:block;font-size:12.5px;margin-top:8px}
</style>
</head>
<body>
<div class="top-bar"></div>

<header class="site-header">
  <a class="brand" href="#"><span class="brand-name">Vantor-i</span><span class="brand-sub">Pty Ltd</span></a>
  <div class="social-top" aria-label="Social links">
    <span class="dot" aria-label="Social link 1"></span>
    <span class="dot" aria-label="Social link 2"></span>
    <span class="dot" aria-label="Social link 3"></span>
    <span class="dot active" aria-label="Social link 4"></span>
  </div>
  <nav class="main-nav">
    <a class="current" href="#">Home</a>
    <a href="#">About</a>
    <a href="#">Services</a>
    <a href="#">Portfolio</a>
    <a href="#">Blog</a>
    <a href="#">Contact</a>
  </nav>
</header>

<section class="hero" role="img" aria-label="Businessman in a suit touching a glowing network of connected business icons on a dark background">
  <h2 class="hero-title">Business Analysis</h2>
  <div class="hero-dots"><span></span><span class="on"></span><span></span><span></span></div>
</section>

<section class="services">
  <div class="service"><div class="badge"><i role="img" aria-label="Team hierarchy icon"></i></div><h3>Project<br>Management</h3></div>
  <div class="service"><div class="badge"><i role="img" aria-label="Presenter and audience icon"></i></div><h3>Business Process<br>Management</h3></div>
  <div class="service active"><div class="badge"><i role="img" aria-label="Two people exchanging icon"></i></div><h3>Change<br>Management</h3></div>
  <div class="service"><div class="badge"><i role="img" aria-label="Person with chart icon"></i></div><h3>Business<br>Analysis</h3></div>
  <div class="service"><div class="badge"><i role="img" aria-label="Person with gears icon"></i></div><h3>Business<br>Intelligence</h3></div>
</section>

<section class="welcome">
  <h2 class="section-title">Welcome to Vantor-i</h2>
  <p>Sed ut perspiciatis unde omnis iste natus error sit voluptatem accusantium doloremque laudantium, totam rem aperiam, eaque ipsa quae ab illo inven-toipsam voluptatem. quia voluptas sit aspernatur aut odit aut fugit, sed quia consequuntur magni dolores eos qui ratione voluptatem</p>
  <div class="tweet">
    <h2 class="section-title">Latest Tweet</h2>
    <p><em>15 mins ago.</em> Contrary to popular belief, Lorem Ipsum is not simply random over 2000 years old. Desmond Halloway <a href="#">@vantornews</a></p>
  </div>
</section>

<section class="news">
  <h2 class="section-title">Latest News &amp; Updates</h2>
  <article class="news-item">
    <div class="news-date">March 26, 2014</div>
    <h4>Sed Perspiciatis Unde Mexplicabo</h4>
    <p>For sit voluptatem accusantium doloremque its mi beatae vitae dicta sunt explicabo <a href="#">... learn more</a></p>
  </article>
  <article class="news-item">
    <div class="news-date">March 22, 2014</div>
    <h4>Accusantium Invento Totam Sitme</h4>
    <p>Laudantium, totam rem aperiam, eaque ipsa quae beatae vitae dicta &nbsp;<a href="#">... learn more</a></p>
  </article>
</section>

<footer class="site-footer">
  <div class="foot-col foot-connect">
    <h5>CONNECT WITH US</h5>
    <div>on social media network</div>
    <div class="foot-social"><span aria-label="Social link 1"></span><span aria-label="Social link 2"></span><span aria-label="Social link 3"></span><span aria-label="Social link 4"></span></div>
  </div>
  <div class="foot-col foot-pages">
    <h5>PAGES</h5>
    <div class="pages-grid">
      <a href="#">Home</a><a href="#">Term &amp; Conditions</a>
      <a href="#">About</a><a href="#">FAQ</a>
      <a href="#">Services</a><a href="#">Porfolio</a>
    </div>
  </div>
  <div class="foot-col foot-contact">
    <h5>CONTACT DETAILS</h5>
    <div>p: +61 3 400 118 522 &nbsp;f: +61 3 9000 4417</div>
    <div>Level 7, 18 Harlow Lane Melbourne,</div>
    <div>Australia, 3000</div>
  </div>
  <div class="foot-brand">
    <span class="brand-name">Vantor-i</span>
    <span class="brand-sub">Pty Ltd</span>
    <small>Copyright © 2014 All Rights Reserved</small>
  </div>
</footer>
</body>
</html>
```